New Mechanical Maintenance business needs website

New Mechanical Maintenance business in Perth Western Australia needs a nice and easy to navigate website. Showing what we do and how we can be the right fit for other small to medium size business by offering personalized service from our highly skilled team. We deal with both fixed plant repairs like food and chemical processing facilities to heavy equipment like drill rigs, Large boats and earthmoving equipment.

Target Market(s)

Small to medium business to offer personalized services/packages

Industry/Entity Type

e deal with both fixed plant repairs like food and chemical processing facilities to heavy equipment like drill rigs, Large boats and earthmoving equipment.

Coding

Coded - Design and coding required

Number of Pages Required

4 page

Font styles to use
Serif

Colors
0054AA
0677BA
7BADD7
CADEEF
E8F1F8

Requirements
Must have
• A website that is easy to navigate but covers off on the range of services/maintenance we can provide

```html
<!DOCTYPE html>
<html lang="en">
<head>
<meta charset="utf-8">
<title>Ardent Maintenance Services</title>
<link href="https://fonts.googleapis.com/css2?family=Roboto:wght@400;500;700&family=Lato:wght@400;700&display=swap" rel="stylesheet">
<style>
:root{
  --blue-deep:#0054AA;
  --blue:#0677BA;
  --blue-mid:#7BADD7;
  --blue-pale:#CADEEF;
  --blue-mist:#E8F1F8;
  --ink:#111;
  --text:#555;
  --grey-bg:#f1f2f4;
  --white:#fff;
  --black:#000;
}
*{margin:0;padding:0;box-sizing:border-box}
html,body{width:1200px;height:4035px;overflow:hidden;background:var(--white)}
body{position:relative;font-family:'Roboto',sans-serif;color:var(--ink)}
.abs{position:absolute}
.photo{position:absolute;border-radius:2px}
.btn{position:absolute;display:flex;align-items:center;justify-content:center;border-radius:20px;font:700 15px 'Roboto',sans-serif;text-decoration:none}
.btn-blue{background:var(--blue);color:var(--white)}
.btn-white{background:var(--white);color:var(--blue-deep)}
.h2{font:700 46px 'Roboto',sans-serif;color:var(--ink);line-height:1}
.para{font:400 15px/26px 'Roboto',sans-serif;color:var(--text)}

/* hero */
.hero{position:absolute;left:0;top:0;width:1200px;height:686px;background:linear-gradient(100deg,#1b1b1d 0%,#2a2b2f 40%,#1e2a4a 65%,#223764 100%)}
.brand{position:absolute;display:flex;align-items:center;gap:12px;color:var(--white);font:700 28px 'Roboto',sans-serif}
.brand .dot{width:22px;height:22px;border-radius:50%;background:var(--white)}
.nav{position:absolute;top:45px;font:400 15px 'Lato',sans-serif;color:var(--white)}
.hero-welcome{left:113px;top:280px;font:500 52px 'Roboto',sans-serif;color:var(--white)}
.hero-title{left:113px;top:354px;font:700 62px/70px 'Roboto',sans-serif;color:var(--white)}

/* services */
.services{position:absolute;left:0;top:1224px;width:1200px;height:652px;background:var(--grey-bg)}
.card-title{position:absolute;font:500 25px 'Roboto',sans-serif;color:var(--blue)}
.card-text{position:absolute;width:285px;font:400 15px/26px 'Roboto',sans-serif;color:#333}
.more{position:absolute;font:700 14px 'Roboto',sans-serif;color:var(--blue)}
.arrow{position:absolute;width:32px;height:32px;border-radius:50%;background:var(--blue)}

/* why */
.why{position:absolute;left:0;top:1876px;width:1200px;height:470px;background:radial-gradient(circle at 70% 40%,#1a84c8 0%,var(--blue) 50%,#0a64a8 100%)}
.why-col{position:absolute;width:210px;text-align:center;color:var(--white)}
.why-col h3{font:700 20px 'Roboto',sans-serif;margin:14px 0 10px}
.why-col p{font:400 14px/26px 'Roboto',sans-serif;width:190px;margin:0 auto}
.why-col a{font:700 14px 'Roboto',sans-serif;color:var(--white);text-decoration:none;display:block;margin-top:4px}

/* footer */
.footer{position:absolute;left:0;top:3629px;width:1200px;height:406px;background:var(--black);color:var(--white)}
.f-head{position:absolute;font:700 20px 'Roboto',sans-serif}
.f-list{position:absolute;list-style:none;font:400 15px/30px 'Roboto',sans-serif}
.f-item{position:absolute;font:400 14px/20px 'Roboto',sans-serif}
</style>
</head>
<body>

<header class="hero">
  <div class="photo" role="img" aria-label="Mechanic in navy overalls and grey gloves holding spanners" style="left:560px;top:0;width:640px;height:686px;background:linear-gradient(120deg,#2a3d6a,#1a2a52 60%,#31477a);border-radius:0"></div>
  <div class="brand" style="left:113px;top:84px"><span class="dot"></span>Ardent</div>
  <a class="nav" style="left:365px">Home</a>
  <a class="nav" style="left:439px">About Us</a>
  <a class="nav" style="left:534px">What We Do</a>
  <a class="nav" style="left:658px">Why Choose Us</a>
  <a class="nav" style="left:801px">Contact Us</a>
  <a class="btn btn-white" style="left:915px;top:38px;width:171px;height:37px">Get Started</a>
  <div class="abs hero-welcome">Welcome To</div>
  <h1 class="abs hero-title">Ardent Maintenance<br>Services Pty Ltd</h1>
  <a class="btn btn-white" style="left:114px;top:526px;width:173px;height:38px">Read More</a>
</header>

<section>
  <h2 class="abs h2" style="left:113px;top:771px">About Us</h2>
  <p class="abs para" style="left:111px;top:843px;width:450px">Lorem ipsum dolor sit amet, consectetur adipiscing elit, sed do eiusmod tempor incididunt ut labore et dolore magna aliqua. Quis ipsum suspendisse ultrices gravida. Risus commodo viverra maecenas accumsan lacus vel facilisis.</p>
  <p class="abs para" style="left:111px;top:961px;width:450px">Sed ut perspiciatis unde omnis iste natus error sit voluptatem accusantium doloremque laudantium, totam rem aperiam, eaque ipsa quae ab illo inventore veritatis et quasi architecto beatae vitae dicta sunt explicabo.</p>
  <a class="btn btn-blue" style="left:111px;top:1097px;width:171px;height:37px">Read More</a>
  <div class="photo" role="img" aria-label="Two technicians in safety glasses servicing an engine" style="left:627px;top:771px;width:462px;height:365px;background:linear-gradient(135deg,#b4bcc8,#4a5a78 55%,#1f3566)"></div>
</section>

<section class="services">
  <h2 class="abs h2" style="left:114px;top:84px">What We Do</h2>
  <span class="arrow" style="left:55px;top:274px"><svg width="32" height="32"><path d="M18 10l-6 6 6 6" stroke="#fff" stroke-width="2.5" fill="none"/></svg></span>
  <span class="arrow" style="left:1113px;top:274px"><svg width="32" height="32"><path d="M14 10l6 6-6 6" stroke="#fff" stroke-width="2.5" fill="none"/></svg></span>

  <div class="photo" role="img" aria-label="Worker repairing a drill rig pipe on a dirt site" style="left:111px;top:167px;width:312px;height:237px;background:linear-gradient(135deg,#9a8268,#c7b194 50%,#6e5c48)"></div>
  <h3 class="card-title" style="left:111px;top:425px">Drill Rigs</h3>
  <p class="card-text" style="left:111px;top:469px">Lorem ipsum dolor sit amet, consectetur adipiscing elit, sed do incididunt ut labore et dolore magna aliqua.</p>
  <a class="more" style="left:111px;top:556px">Read More....</a>

  <div class="photo" role="img" aria-label="Large boat lifted by a yellow gantry crane" style="left:443px;top:167px;width:312px;height:237px;background:linear-gradient(180deg,#2f8ae0,#6eb0ee 55%,#c9c08a)"></div>
  <h3 class="card-title" style="left:443px;top:425px">Large Boats</h3>
  <p class="card-text" style="left:443px;top:469px">Lorem ipsum dolor sit amet, consectetur adipiscing elit, sed do incididunt ut labore et dolore magna aliqua.</p>
  <a class="more" style="left:443px;top:556px">Read More....</a>

  <div class="photo" role="img" aria-label="Technician climbing a yellow excavator" style="left:776px;top:167px;width:311px;height:237px;background:linear-gradient(160deg,#7f95b5,#c9cfd8 45%,#d4a93a)"></div>
  <h3 class="card-title" style="left:776px;top:425px">Earthmoving Equipment</h3>
  <p class="card-text" style="left:776px;top:469px">Lorem ipsum dolor sit amet, consectetur adipiscing elit, sed do incididunt ut labore et dolore magna aliqua.</p>
  <a class="more" style="left:776px;top:556px">Read More....</a>
</section>

<section class="why">
  <h2 class="abs h2" style="left:0;width:1200px;text-align:center;top:88px;color:var(--white)">Why Choose Us</h2>
  <div class="why-col" style="left:99px;top:176px">
    <svg width="56" height="56" viewBox="0 0 56 56"><circle cx="28" cy="28" r="15" fill="none" stroke="#fff" stroke-width="8" stroke-dasharray="6 4"/><circle cx="28" cy="28" r="6" fill="#fff"/></svg>
    <h3>Finibus Bonorum</h3>
    <p>Lorem ipsum dolor sit amet, consectetur adipiscing elit, magna aliqua.</p>
    <a>Learn More...</a>
  </div>
  <div class="why-col" style="left:364px;top:176px">
    <svg width="56" height="56" viewBox="0 0 56 56"><path d="M12 28a16 16 0 0 1 32 0z" fill="#fff"/><rect x="10" y="28" width="36" height="4" fill="#fff"/><rect x="14" y="38" width="28" height="16" rx="4" fill="#fff"/></svg>
    <h3>Nemo Enim Ipsam</h3>
    <p>Lorem ipsum dolor sit amet, consectetur elit, magna aliqua.</p>
    <a>Learn More...</a>
  </div>
  <div class="why-col" style="left:625px;top:176px">
    <svg width="56" height="56" viewBox="0 0 56 56"><path d="M10 10l36 36M46 10L10 46" stroke="#fff" stroke-width="7" stroke-linecap="round"/><circle cx="28" cy="28" r="7" fill="#fff"/></svg>
    <h3>Duis aute irure dolor</h3>
    <p>Lorem ipsum dolor sit amet, consectetur adipiscing elit, magna aliqua.</p>
    <a>Learn More...</a>
  </div>
  <div class="why-col" style="left:889px;top:176px">
    <svg width="56" height="56" viewBox="0 0 56 56"><path d="M12 30l10 10 22-24" stroke="#fff" stroke-width="7" fill="none" stroke-linecap="round" stroke-linejoin="round"/></svg>
    <h3>Excepteur sint</h3>
    <p>Lorem ipsum dolor sit amet, consectetur adipiscing magna aliqua.</p>
    <a>Learn More...</a>
  </div>
</section>

<section>
  <h2 class="abs h2" style="left:0;width:1200px;text-align:center;top:2428px">Our Gallery</h2>
  <div class="photo" role="img" aria-label="Two engineers in hard hats inspecting machinery" style="left:113px;top:2518px;width:305px;height:234px;background:linear-gradient(135deg,#c2c4c6,#6c7480 50%,#1f2633)"></div>
  <div class="photo" role="img" aria-label="Worker with yellow gloves fixing a hydraulic arm" style="left:447px;top:2518px;width:307px;height:234px;background:linear-gradient(135deg,#8fa1b6,#c99a3a 50%,#5a4430)"></div>
  <div class="photo" role="img" aria-label="Boat hull under scaffolding in a workshop" style="left:782px;top:2518px;width:305px;height:234px;background:linear-gradient(180deg,#9aa3ad,#d4d8dc 50%,#3f6e9a)"></div>
  <div class="photo" role="img" aria-label="Grader on site at sunset" style="left:113px;top:2781px;width:305px;height:234px;background:linear-gradient(160deg,#d8c7a8,#b48b44 50%,#3a3128)"></div>
  <div class="photo" role="img" aria-label="Worker with tablet in front of a ship hull" style="left:447px;top:2781px;width:307px;height:234px;background:linear-gradient(150deg,#2e5c70,#8c4a46 50%,#4a4040)"></div>
  <div class="photo" role="img" aria-label="Worker handling drill pipe at an oil rig" style="left:782px;top:2781px;width:305px;height:234px;background:linear-gradient(180deg,#a8abb0,#c6c8cb 45%,#6a5a40)"></div>
  <a class="btn btn-blue" style="left:517px;top:3053px;width:169px;height:37px">View All</a>
</section>

<section>
  <div class="photo" role="img" aria-label="Mechanic inspecting the underside of a lifted car" style="left:113px;top:3180px;width:461px;height:363px;background:linear-gradient(150deg,#7a8797,#c2cad4 45%,#23406e)"></div>
  <h2 class="abs h2" style="left:639px;top:3179px">Where We Come From</h2>
  <p class="abs para" style="left:646px;top:3249px;width:442px">Director of the company has over 20-year experience in the fixed and mobile plant industries ranging from Perth local and overseas. Facilities like precious metals refining, offshore drilling and production platform, open cut and underground mining, civils, geotechnical and construction equipment and large-scale construction as an</p>
  <p class="abs para" style="left:646px;top:3419px;width:442px">We offer personalised service to all small and medium size business across a diverse range of industries.</p>
  <a class="btn btn-blue" style="left:638px;top:3504px;width:171px;height:37px">Read More</a>
</section>

<footer class="footer">
  <div class="brand" style="left:113px;top:138px;font-size:34px"><span class="dot" style="width:28px;height:28px"></span>Ardent</div>
  <h4 class="f-head" style="left:483px;top:88px">Links</h4>
  <ul class="f-list" style="left:483px;top:126px">
    <li>Home</li><li>About Us</li><li>What We Do</li><li>Why Choose Us</li><li>Contact Us</li>
  </ul>
  <h4 class="f-head" style="left:713px;top:85px">Contact Us</h4>
  <svg class="abs" style="left:682px;top:129px" width="14" height="14" viewBox="0 0 14 14"><path d="M3 1l3 3-2 2a8 8 0 0 0 4 4l2-2 3 3-2 2C6 13 1 8 1 3z" fill="var(--blue)"/></svg>
  <div class="f-item" style="left:713px;top:126px">+61 8 9000 0000</div>
  <svg class="abs" style="left:682px;top:170px" width="14" height="10" viewBox="0 0 14 10"><rect x="0.5" y="0.5" width="13" height="9" fill="none" stroke="var(--blue)"/><path d="M1 1l6 5 6-5" stroke="var(--blue)" fill="none"/></svg>
  <div class="f-item" style="left:713px;top:165px">hello@ardentmaint.example</div>
  <svg class="abs" style="left:683px;top:206px" width="12" height="16" viewBox="0 0 12 16"><path d="M6 0a6 6 0 0 1 6 6c0 4-6 10-6 10S0 10 0 6a6 6 0 0 1 6-6z" fill="var(--blue)"/><circle cx="6" cy="6" r="2" fill="#000"/></svg>
  <div class="f-item" style="left:713px;top:204px;width:160px">12 Forge Street,<br>Welshpool WA 6106.</div>
  <h4 class="f-head" style="left:990px;top:88px">Follow Us</h4>
  <ul class="f-list" style="left:990px;top:126px;font-size:14px;line-height:26px">
    <li>Workshop Feed</li><li>Trade Network</li><li>Photo Journal</li>
  </ul>
  <div class="abs" style="left:0;top:367px;width:1200px;height:1px;background:#444"></div>
  <div class="abs" style="left:0;top:380px;width:1200px;text-align:center;font:400 13px 'Roboto',sans-serif">© 2024 Ardent Maintenance. All rights reserved</div>
</footer>

</body>
</html>
```